Business Card Design Project

Business card based on attached logo

Todd Merrick
Todd@lorvantest.com
877-514-9073 ext. 318
Www.LorvanTest.com

Industry/Entity Type

Business

```html
<!DOCTYPE html>
<html lang="en">
<head>
<meta charset="utf-8">
<title>LorvanTest Business Cards</title>
<link rel="stylesheet" href="https://fonts.googleapis.com/css2?family=Arimo:wght@400;700&display=swap">
<style>
  :root {
    --stage: #8b8d90;
    --ink: #231f20;
    --red: #e32227;
    --red-deep: #c4161c;
    --paper: #ffffff;
    --charcoal: #2a2a2a;
    --charcoal-light: #4a4a4a;
    --rule: #c9c9c9;
  }
  * { margin: 0; padding: 0; box-sizing: border-box; }
  html, body {
    width: 1200px; height: 720px; overflow: hidden;
    background: var(--stage);
    font-family: "Arimo", Arial, sans-serif;
  }
  .sheet { position: relative; width: 1200px; height: 720px; }
  .card {
    position: absolute; width: 564px; height: 321px;
    border-radius: 20px; overflow: hidden;
  }
  .card--front { left: 30px; top: 27px; background: var(--paper); }
  .card--white { left: 615px; top: 27px; background: var(--paper); border: 1px solid #7a7a7a; }
  .card--dark { left: 31px; top: 372px; background: radial-gradient(ellipse at 50% 45%, var(--charcoal-light), var(--charcoal) 70%, #1c1c1c); }
  .card--red { left: 612px; top: 372px; background: linear-gradient(135deg, var(--red) 0%, var(--red-deep) 100%); }

  .wordmark { position: absolute; font-weight: 700; letter-spacing: -1px; white-space: nowrap; line-height: 1; }
  .wordmark__square { position: absolute; width: 26px; height: 26px; }

  /* front card */
  .card--front .wordmark { left: 32px; top: 112px; font-size: 44px; color: var(--ink); }
  .card--front .wordmark__square { left: 258px; top: 76px; background: var(--red); }
  .divider { position: absolute; left: 298px; top: 74px; width: 1px; height: 124px; background: var(--rule); }
  .contact { position: absolute; left: 326px; top: 104px; list-style: none; color: var(--ink); font-size: 17px; }
  .contact li { display: flex; align-items: center; height: 27.5px; }
  .contact svg { width: 13px; height: 13px; margin-right: 10px; flex: none; }
  .wave { position: absolute; left: 0; bottom: 0; width: 564px; height: 321px; }
  .holder { position: absolute; left: 52px; top: 297px; color: var(--paper); font-size: 19px; letter-spacing: 0.3px; }

  /* logo cards */
  .card--white .wordmark { left: 0; right: 0; top: 118px; text-align: center; font-size: 76px; color: var(--ink); }
  .card--white .wordmark__square { left: 440px; top: 60px; width: 40px; height: 40px; background: var(--red); }
  .card--dark .wordmark { left: 0; right: 0; top: 126px; text-align: center; font-size: 72px; color: var(--paper); }
  .card--dark .wordmark__square { left: 432px; top: 74px; width: 38px; height: 38px; background: var(--paper); }
  .card--red .wordmark { left: 34px; top: 60px; font-size: 76px; color: var(--paper); }
  .faint-square { position: absolute; left: 418px; top: 168px; width: 150px; height: 150px; background: rgba(255,255,255,0.12); }

  .url { position: absolute; font-size: 17px; letter-spacing: 3px; white-space: nowrap; }
  .card--white .url { left: 0; right: 0; top: 286px; text-align: center; color: var(--ink); }
  .card--dark .url { left: 0; right: 0; top: 286px; text-align: center; color: var(--paper); }
  .card--red .url { left: 36px; top: 286px; color: var(--paper); }
</style>
</head>
<body>
<main class="sheet">

  <section class="card card--front">
    <span class="wordmark__square"></span>
    <span class="wordmark">LorvanTest</span>
    <span class="divider"></span>
    <ul class="contact">
      <li>
        <svg viewBox="0 0 16 16"><circle cx="8" cy="8" r="7" fill="none" stroke="#e32227" stroke-width="1.6"/><path d="M5 4.5l2 2-1 1c.6 1.2 1.3 1.9 2.5 2.5l1-1 2 2-1.3 1.3C7 12 4 9 3.7 5.8z" fill="#e32227"/></svg>
        877-514-9073 ext. 318
      </li>
      <li>
        <svg viewBox="0 0 16 16"><path d="M1 6l7-4 7 4v8H1z" fill="#e32227"/><path d="M1 6l7 5 7-5" fill="none" stroke="#fff" stroke-width="1.3"/></svg>
        Todd@lorvantest.com
      </li>
      <li>
        <svg viewBox="0 0 16 16"><circle cx="8" cy="8" r="6.5" fill="none" stroke="#e32227" stroke-width="1.4"/><ellipse cx="8" cy="8" rx="3" ry="6.5" fill="none" stroke="#e32227" stroke-width="1.2"/><path d="M1.5 8h13M2.5 5h11M2.5 11h11" stroke="#e32227" stroke-width="1"/></svg>
        www.lorvantest.com
      </li>
    </ul>
    <svg class="wave" viewBox="0 0 564 321" preserveAspectRatio="none" aria-hidden="true">
      <path d="M0,252 C160,240 320,282 440,300 C500,308 540,298 564,282 L564,321 L0,321 Z" fill="#e32227"/>
      <path d="M0,262 C160,252 310,292 430,310 C490,318 535,310 564,298 L564,321 L0,321 Z" fill="#ffffff"/>
      <path d="M0,268 C160,260 300,296 420,316 C490,326 535,318 564,306 L564,321 L0,321 Z" fill="#231f20"/>
    </svg>
    <span class="holder">TODD MERRICK</span>
  </section>

  <section class="card card--white">
    <span class="wordmark__square"></span>
    <span class="wordmark">LorvanTest</span>
    <span class="url">www.lorvantest.com</span>
  </section>

  <section class="card card--dark">
    <span class="wordmark__square"></span>
    <span class="wordmark">LorvanTest</span>
    <span class="url">www.lorvantest.com</span>
  </section>

  <section class="card card--red">
    <span class="faint-square"></span>
    <span class="wordmark">LorvanTest</span>
    <span class="url">www.lorvantest.com</span>
  </section>

</main>
</body>
</html>
```